Business Card Design Project

I need a business card designed from scratch. I have an existing logo that I can upload in Illustrator for modification or redesign.

The Company is called Query Lanterns http://querylanterns.com.au and we provide Search Engine Optimization services to Australian businesses. The current logo signifies an increase in visitors, profits etc...

There are no restrictions as to the redesign - colours, style etc are all open to change.

Cards will be full colour and one sided printed at http://www.cardmoxel.com.au so check their requirements for file format and sizes etc.

I will expect all original files upon completion of project.

Target Market(s)

Any business with a web site looking to improve their search engine rankings

Industry/Entity Type

Business

Requirements
Must have
• I like modern, sleek designs. Clean, not fussy, uncluttered.

```html
<!DOCTYPE html>
<html lang="en">
<head>
<meta charset="utf-8">
<title>Query Lanterns – Business Card</title>
<link href="https://fonts.googleapis.com/css2?family=Open+Sans:wght@400;600;700;800&display=swap" rel="stylesheet">
<style>
  :root {
    --backdrop: #4a2e1c;
    --card: #ffffff;
    --brand-blue: #1f6fb8;
    --deep-blue: #1c3a6b;
    --mid-blue: #2f86c8;
    --brand-yellow: #f6bf1a;
    --ink: #2b2b2b;
    --ink-soft: #3a3a3a;
  }
  * { box-sizing: border-box; margin: 0; padding: 0; }
  html, body {
    width: 1200px; height: 412px; overflow: hidden;
    background: var(--backdrop);
    font-family: "Open Sans", Arial, sans-serif;
  }
  .canvas { position: relative; width: 1200px; height: 412px; }
  .card {
    position: absolute; top: 65px;
    width: 497px; height: 284px;
    background: var(--card);
    overflow: hidden;
  }
  .card--front { left: 73px; }
  .card--back { left: 631px; }

  .brand-name {
    position: absolute;
    display: flex; align-items: center; gap: 8px;
    font-weight: 800; color: var(--brand-blue);
    white-space: nowrap; line-height: 1;
  }
  .brand-name__dot {
    width: 12px; height: 12px; border-radius: 50%;
    background: var(--brand-yellow);
  }
  .card--front .brand-name { left: 30px; top: 56px; font-size: 27px; }
  .card--back .brand-name { left: 0; right: 0; top: 96px; justify-content: center; font-size: 34px; }

  .contact-list {
    position: absolute; left: 30px; top: 136px;
    list-style: none; font-size: 12px; color: var(--ink);
    line-height: 17.5px;
  }
  .contact-list li { display: flex; align-items: center; gap: 6px; }
  .contact-list svg { width: 10px; height: 10px; fill: var(--ink); }

  .address {
    position: absolute; left: 30px; top: 212px;
    font-size: 12px; line-height: 18px; color: var(--ink);
    font-style: normal;
  }

  .accent-field {
    position: absolute; left: 330px; top: 150px;
    width: 167px; height: 134px;
    background: linear-gradient(160deg, var(--mid-blue) 0%, var(--deep-blue) 100%);
    border-top: 6px solid var(--brand-yellow);
  }

  .holder {
    position: absolute; right: 28px; top: 232px;
    text-align: center; color: #fff;
  }
  .holder__name { font-size: 16px; font-weight: 700; line-height: 20px; }
  .holder__title { font-size: 13px; font-weight: 400; line-height: 18px; }

  .web-address {
    position: absolute; left: 0; right: 0; top: 236px;
    text-align: center; font-size: 12px; font-weight: 700;
    letter-spacing: 3.4px; color: var(--ink-soft);
  }
</style>
</head>
<body>
<main class="canvas">

  <section class="card card--front" aria-label="Card front">
    <div class="accent-field" role="img" aria-label="Decorative blue and yellow wave area"></div>

    <div class="brand-name"><span class="brand-name__dot"></span>Query Lanterns</div>

    <ul class="contact-list">
      <li><svg viewBox="0 0 10 10"><circle cx="5" cy="5" r="4.5" fill="none" stroke="#2b2b2b"/><path d="M3 3h1.5l.5 1.5-1 .8c.4.8 1 1.4 1.8 1.8l.8-1 1.5.5V8C5 8 2.5 5.5 3 3z"/></svg>098 765 4321</li>
      <li><svg viewBox="0 0 10 10"><rect x="2.5" y="0.5" width="5" height="9" rx="1"/><rect x="3.5" y="1.8" width="3" height="5" fill="#fff"/></svg>098 765 4321</li>
      <li><svg viewBox="0 0 10 10"><rect x="0.5" y="2" width="9" height="6.5" rx="1"/><path d="M1 2.5l4 3 4-3" stroke="#fff" fill="none"/></svg>enquiry@querylanterns.com.au</li>
      <li><svg viewBox="0 0 10 10"><circle cx="5" cy="5" r="4.5"/><path d="M0.5 5h9M5 0.5c-2 2.5-2 6.5 0 9M5 0.5c2 2.5 2 6.5 0 9" stroke="#fff" stroke-width="0.7" fill="none"/></svg>www.querylanterns.com.au</li>
    </ul>

    <address class="address">Complex name,Street name<br>City, State, zip code</address>

    <div class="holder">
      <div class="holder__name">Your Name</div>
      <div class="holder__title">Title</div>
    </div>
  </section>

  <section class="card card--back" aria-label="Card back">
    <div class="brand-name"><span class="brand-name__dot"></span>Query Lanterns</div>
    <div class="web-address">www.querylanterns.com.au</div>
  </section>

</main>
</body>
</html>
```